BOLD & MINIMALIST DESIGN NEEDED

We want a very bold but minimalistic business card design that is impactful and utilizes both sides of the business card. Our current logo is included for your use.

We want bold fonts and good use of negative space. We don't want the logo to overpower the design.

Target Market(s)

Professionals who are building new commercial buildings.

Industry/Entity Type

Construction

Contact Information for Business Card

Name, Title, email, office phone, cell phone, website

Font styles to use
Serif
Sans Serif

Requirements
Must have
• Bold design!

```html
<!DOCTYPE html>
<html lang="en">
<head>
<meta charset="utf-8">
<title>Crestline — Business Card</title>
<link rel="stylesheet" href="https://fonts.googleapis.com/css2?family=Montserrat:wght@400;500;700;800&display=swap">
<style>
  :root {
    --canvas-bg: #a3a3a3;
    --card-white: #ffffff;
    --brand-green: #86c440;
    --brand-green-deep: #7dbb3a;
    --name-pale: #e6f4d2;
    --ink: #1a1a1a;
    --ink-soft: #3a3a3a;
  }
  * { box-sizing: border-box; margin: 0; padding: 0; }
  html, body {
    width: 1200px;
    height: 946px;
    overflow: hidden;
  }
  body {
    background: var(--canvas-bg);
    font-family: "Montserrat", Arial, sans-serif;
    display: flex;
    flex-direction: column;
    align-items: center;
    justify-content: center;
    gap: 40px;
  }
  .card {
    width: 700px;
    height: 400px;
    border-radius: 26px;
    position: relative;
    overflow: hidden;
  }

  /* Front */
  .card-front {
    background: var(--brand-green);
    display: flex;
    align-items: center;
    justify-content: center;
  }
  .card-front .brand-name {
    font-weight: 800;
    font-size: 64px;
    letter-spacing: 2px;
    color: var(--name-pale);
  }

  /* Back */
  .card-back {
    background: var(--card-white);
  }
  .card-back .brand-name {
    position: absolute;
    left: 206px;
    top: 241px;
    transform: translate(-50%, -50%);
    font-weight: 800;
    font-size: 40px;
    letter-spacing: 1px;
    color: var(--ink);
  }
  .divider {
    position: absolute;
    left: 374px;
    top: 78px;
    width: 2px;
    height: 246px;
    background: var(--brand-green-deep);
  }
  .contact {
    position: absolute;
    left: 402px;
    top: 70px;
    color: var(--ink-soft);
  }
  .contact .person-name {
    font-weight: 700;
    font-size: 32px;
    color: var(--brand-green-deep);
    line-height: 1.1;
  }
  .contact .person-title {
    font-size: 19px;
    margin-top: 8px;
  }
  .contact address {
    font-style: normal;
    font-size: 19px;
    line-height: 28px;
    margin-top: 16px;
  }
  .contact .lines {
    list-style: none;
    margin-top: 14px;
    font-size: 19px;
    line-height: 28px;
  }
  .contact .lines li {
    display: flex;
    align-items: center;
    gap: 9px;
  }
  .contact .lines svg {
    width: 14px;
    height: 14px;
    fill: var(--brand-green-deep);
    flex: none;
  }
</style>
</head>
<body>

  <section class="card card-front" aria-label="Business card front">
    <span class="brand-name">CRESTLINE</span>
  </section>

  <section class="card card-back" aria-label="Business card back">
    <span class="brand-name">CRESTLINE</span>
    <div class="divider"></div>
    <div class="contact">
      <p class="person-name">DANIEL REYES</p>
      <p class="person-title">OWNER-CEO</p>
      <address>Your address, City<br>State, Zip 1234</address>
      <ul class="lines">
        <li>
          <svg viewBox="0 0 16 16" aria-hidden="true"><path d="M1 6c0-2 3-4 7-4s7 2 7 4v1h-4V5.5H5V7H1zM3 8h10l1 6H2z"/></svg>
          123 456 789
        </li>
        <li>
          <svg viewBox="0 0 16 16" aria-hidden="true"><path d="M4 0h8a1 1 0 0 1 1 1v14a1 1 0 0 1-1 1H4a1 1 0 0 1-1-1V1a1 1 0 0 1 1-1zm1 2v10h6V2z"/></svg>
          123 456 789
        </li>
        <li>
          <svg viewBox="0 0 16 16" aria-hidden="true"><path d="M1 3h14v1L8 9 1 4zm0 3 7 5 7-5v7H1z"/></svg>
          info@youremail.com
        </li>
        <li>
          <svg viewBox="0 0 16 16" aria-hidden="true"><path d="M8 0a8 8 0 1 0 0 16A8 8 0 0 0 8 0zm0 2a6 6 0 0 1 5.7 4H10L8 4 6 5 4 3.5A6 6 0 0 1 8 2zM2.5 9 5 10l1 3-1 1A6 6 0 0 1 2.5 9zM10 13l1-3h2.8A6 6 0 0 1 10 13z"/></svg>
          www.yourwebsite.com
        </li>
      </ul>
    </div>
  </section>

</body>
</html>
```